K7 Electrical Services Ltd Web design

I require a web site for my new electrical contracting company. We are customer service orientated. Offering high value electrical installations, design and maintenance. Focused on custom residential and commercial upgrading. Lighting design and application are paramount in our company's services. Industry leading product use and integration are always on the forefront with our customer client services. As well as energy efficiency.

Target Market(s)

Homebuilders, General Contractors, Property management companies, clients, individuals,

Industry/Entity Type

Electric Company

Coding

Coded - Design and coding required

Number of Pages Required

3 page

Requirements
Must have
• Classic, modern, edgy but not trendy . Appeals to the masse.
• 3 page
• home page
• about page
• gallery page
• ability to contact from the webiste
Nice to have
• open to all types of designs that are relative to the construction industry.
• Black, Grey, metallic ice blue and deep purple colours from the logo.
Should not have
• anything cheesy with cartoon light bulb images.

```html
<!DOCTYPE html>
<html lang="en">
<head>
<meta charset="utf-8">
<title>K7 Electrical Services</title>
<link rel="stylesheet" href="https://fonts.googleapis.com/css2?family=Lato:wght@400;700&family=Open+Sans:wght@400;600;700&display=swap">
<style>
:root{
  --purple:#5e2b8c;
  --purple-dark:#4b2173;
  --ink:#111111;
  --text:#555555;
  --muted:#888888;
  --light:#f0f0f0;
  --band:#eef1f4;
  --white:#ffffff;
  --line:#dddddd;
}
*{margin:0;padding:0;box-sizing:border-box}
html,body{width:1200px;height:2452px;overflow:hidden;background:var(--white)}
body{font-family:"Open Sans",Arial,sans-serif;color:var(--text);position:relative}
section,header,footer{position:absolute;left:0;width:1200px}
.abs{position:absolute}

/* header */
.site-header{top:0;height:123px;background:var(--white)}
.brand{left:98px;top:30px;display:flex;align-items:center;gap:12px}
.brand-mark{width:26px;height:26px;background:var(--purple)}
.brand-name{font-family:"Lato",sans-serif;font-weight:700;font-size:24px;color:var(--purple);letter-spacing:.5px}
.social{display:flex;gap:7px}
.social span{width:18px;height:18px;border-radius:50%;background:var(--purple);display:block}
.header-social{right:100px;top:17px}
.contact-line{right:100px;top:53px;font-size:14px;color:var(--muted);display:flex;gap:14px;align-items:center}
.contact-line .sep{color:var(--line)}
.contact-line svg{vertical-align:-2px;margin-right:8px}
.main-nav{right:96px;top:88px;display:flex;gap:24px;font-size:16px;color:var(--ink);align-items:center}

/* hero */
.hero{top:123px;height:479px;background:linear-gradient(90deg,#e9ecef 0%,#f7f8f9 40%,#eceff2 100%);overflow:hidden}
.hero-photo{position:absolute;left:0;top:0;width:540px;height:479px;background:linear-gradient(160deg,#d9dde2,#b6a98f 60%,#7a6b58);clip-path:polygon(0 0,540px 0,400px 479px,0 479px)}
.hero-title{left:538px;top:114px;font-family:"Lato",sans-serif;font-weight:700;font-size:59px;color:var(--ink);letter-spacing:-.3px}
.hero-sub{left:542px;top:198px;font-weight:600;font-size:25px;line-height:40px;color:var(--ink)}
.btn-primary{left:538px;top:304px;width:160px;height:46px;border-radius:23px;background:var(--purple);color:var(--white);font-weight:700;font-size:17px;display:flex;align-items:center;justify-content:center}
.hero-arrow{top:221px;width:38px;height:38px;border-radius:50%;background:rgba(180,180,180,.6);display:flex;align-items:center;justify-content:center}

/* about */
.about{top:602px;height:425px;text-align:center}
.section-title{font-family:"Lato",sans-serif;font-weight:700;font-size:30px;color:var(--ink)}
.about .section-title{position:absolute;left:0;width:1200px;top:82px}
.about-text{left:159px;width:882px;top:140px;font-size:13.5px;line-height:29.5px;color:var(--text)}
.btn-outline{left:544px;top:297px;width:112px;height:36px;border:2px solid var(--purple);border-radius:18px;color:var(--purple-dark);font-weight:700;font-size:13.5px;display:flex;align-items:center;justify-content:center}

/* services */
.services{top:1027px;height:420px;background:linear-gradient(180deg,#f3f5f7,#e8ecf0);overflow:hidden}
.services-photo{position:absolute;right:0;top:0;width:420px;height:420px;background:linear-gradient(150deg,#c9b07a,#e0c040 45%,#8f8f96 80%,#c23b3b);clip-path:polygon(120px 0,420px 0,420px 420px,0 420px)}
.service{position:absolute;top:86px;width:240px;text-align:center}
.service svg{display:block;margin:0 auto}
.service h3{font-family:"Lato",sans-serif;font-weight:400;font-size:21px;color:var(--ink);margin-top:16px}
.service p{font-size:14px;line-height:29.5px;margin-top:8px;color:var(--text)}
.service .more{display:inline-block;margin-top:7px;font-size:14px;color:var(--purple-dark)}

/* projects */
.projects{top:1447px;height:544px;text-align:center}
.projects .section-title{position:absolute;left:0;width:1200px;top:86px;font-size:31px}
.filters{left:0;width:1200px;top:148px;font-size:14px;color:var(--text);display:flex;justify-content:center;gap:10px}
.filters .active{color:var(--purple);position:relative}
.filters .active::after{content:"";position:absolute;left:50%;top:22px;margin-left:-5px;border:5px solid transparent;border-top-color:var(--purple)}
.card{position:absolute;top:214px;width:232px;height:236px;background:var(--white);border:2px solid #e2e2e2;box-shadow:0 1px 4px rgba(0,0,0,.08)}
.card-photo{position:absolute;left:4px;top:4px;width:220px;height:172px}
.card-caption{position:absolute;left:0;width:228px;top:196px;font-size:13px;font-style:italic;color:var(--ink);display:flex;justify-content:center;align-items:center;gap:10px}

/* footer */
.site-footer{top:1991px;height:368px;background:var(--light);overflow:hidden}
.newsletter-panel{position:absolute;left:0;top:0;width:460px;height:368px;background:var(--purple);clip-path:polygon(106px 0,458px 0,352px 368px,0 368px)}
.newsletter{left:100px;top:80px;width:270px;color:var(--white)}
.newsletter h4{font-family:"Lato",sans-serif;font-weight:400;font-size:21px}
.newsletter p{font-size:13.5px;line-height:25px;margin-top:14px}
.field{width:266px;height:33px;background:var(--white);color:#777;font-size:12px;padding:9px 14px;margin-top:13px}
.field + .field{margin-top:13px}
.newsletter .subscribe{display:inline-block;margin-top:20px;font-weight:700;font-size:14px;text-decoration:underline}
.footer-col{top:78px}
.footer-col h4{font-family:"Lato",sans-serif;font-weight:400;font-size:21px;color:#555}
.footer-col ul{list-style:none;margin-top:19px}
.footer-col li{font-size:13.5px;color:#666;line-height:29.5px;display:flex;align-items:center}
.footer-col li::before{content:"";width:4px;height:4px;border-radius:50%;background:#aaa;margin-right:18px}
.footer-col.contact li::before{display:none}
.footer-col.contact li svg{margin-right:16px}

.bottom-bar{top:2359px;height:93px;text-align:center}
.bottom-social{left:0;width:1200px;top:35px;display:flex;justify-content:center}
.copyright{left:0;width:1200px;top:66px;font-size:12.5px;color:#555}
</style>
</head>
<body>

<header class="site-header">
  <div class="brand abs"><span class="brand-mark"></span><span class="brand-name">K7 Electrical Services</span></div>
  <div class="social header-social abs"><span></span><span></span><span></span><span></span><span></span></div>
  <div class="contact-line abs">
    <span><svg width="14" height="11" viewBox="0 0 14 11"><rect x="0" y="0" width="14" height="11" fill="#999"/><path d="M0 0 7 6 14 0" fill="none" stroke="#fff" stroke-width="1.4"/></svg>contact@k7electrical.com</span>
    <span class="sep">|</span>
    <span><svg width="12" height="12" viewBox="0 0 24 24"><path fill="#999" d="M6.6 10.8a15 15 0 0 0 6.6 6.6l2.2-2.2a1 1 0 0 1 1-.25 11.4 11.4 0 0 0 3.6.57 1 1 0 0 1 1 1V20a1 1 0 0 1-1 1A17 17 0 0 1 3 4a1 1 0 0 1 1-1h3.5a1 1 0 0 1 1 1c0 1.25.2 2.45.57 3.57a1 1 0 0 1-.25 1z"/></svg>0230555147</span>
  </div>
  <nav class="main-nav abs">
    <span>Home</span><span>About Us</span><span>Services</span><span>Blog</span><span>Contact Us</span>
    <svg width="16" height="16" viewBox="0 0 16 16"><circle cx="6.5" cy="6.5" r="4.8" fill="none" stroke="#111" stroke-width="2.2"/><path d="M10 10l4.5 4.5" stroke="#111" stroke-width="2.6"/></svg>
  </nav>
</header>

<section class="hero">
  <div class="hero-photo" role="img" aria-label="Smiling electrician in a hard hat and tool belt holding pliers"></div>
  <h1 class="hero-title abs">K7 Electrical Services</h1>
  <p class="hero-sub abs">Sed ut perspiciatis unde omnis iste natus error<br>sit voluptatem accusantium doloremque</p>
  <a class="btn-primary abs">Contact Now</a>
  <span class="hero-arrow abs" style="left:27px"><svg width="10" height="12" viewBox="0 0 10 12"><path d="M7 1 2 6l5 5" fill="none" stroke="#fff" stroke-width="2.4"/></svg></span>
  <span class="hero-arrow abs" style="left:1129px"><svg width="10" height="12" viewBox="0 0 10 12"><path d="M3 1l5 5-5 5" fill="none" stroke="#fff" stroke-width="2.4"/></svg></span>
</section>

<section class="about">
  <h2 class="section-title">About Us</h2>
  <p class="about-text abs">At vero eos et accusamus et iusto odio dignissimos ducimus qui blanditiis praesentium voluptatum deleniti atque quos dolores et quas molestias excepturi sint occaecati cupiditate non provident, similique sunt in culpa qui officia deserunt mollitia animi, id est laborum et dolorum fuga. Et harum quidem rerum facilis est et expedita distinctio. Nam libero tempore, cum soluta nobis est eligendi optio cumque nihil impedit quo minus id quod maxime placeat facere possimus, omnis voluptas</p>
  <a class="btn-outline abs">Read More</a>
</section>

<section class="services">
  <div class="services-photo" role="img" aria-label="Close-up of pliers, terminal blocks and coloured electrical wires"></div>

  <div class="service" style="left:92px">
    <svg width="68" height="68" viewBox="0 0 68 68" fill="none" stroke="#5e2b8c" stroke-width="2.4">
      <rect x="20" y="20" width="28" height="28"/><rect x="28" y="28" width="12" height="12"/>
      <circle cx="8" cy="8" r="4"/><circle cx="60" cy="8" r="4"/><circle cx="8" cy="60" r="4"/><circle cx="60" cy="60" r="4"/>
      <path d="M11 11l9 9M57 11l-9 9M11 57l9-9M57 57l-9-9M34 8v12M34 48v12"/>
    </svg>
    <h3>Electrical Installations</h3>
    <p>At vero eos et accusamus et<br>iusto odio dignissimos ducimus qui<br>blanditiis praesentium</p>
    <span class="more">Read More &#10141;</span>
  </div>

  <div class="service" style="left:366px">
    <svg width="68" height="68" viewBox="0 0 68 68" fill="none" stroke="#5e2b8c" stroke-width="2.4">
      <circle cx="34" cy="34" r="31"/>
      <path d="M26 18v10M42 18v10M22 28h24v8a12 12 0 0 1-24 0z M34 48v8"/>
    </svg>
    <h3>Design</h3>
    <p>At vero eos et accusamus et<br>iusto odio dignissimos ducimus qui<br>blanditiis praesentium</p>
    <span class="more">Read More &#10141;</span>
  </div>

  <div class="service" style="left:640px">
    <svg width="68" height="68" viewBox="0 0 68 68" fill="none" stroke="#5e2b8c" stroke-width="2.4">
      <path d="M18 14l22 14-10 16-22-14z M22 6l6 4M32 12l6 4 M30 44l6 10 M40 28l12 8 M36 54l20 10"/>
    </svg>
    <h3>Maintenance</h3>
    <p>At vero eos et accusamus et<br>iusto odio dignissimos ducimus qui<br>blanditiis praesentium</p>
    <span class="more">Read More &#10141;</span>
  </div>
</section>

<section class="projects">
  <h2 class="section-title">Our Projects</h2>
  <div class="filters abs">
    <span class="active">ALL</span><span>/</span><span>HOUSEHOLD</span><span>/</span><span>ORGANIZATION</span><span>/</span><span>RESEARCH</span><span>/</span><span>ELECTRICAL SERVICES</span>
  </div>

  <div class="card" style="left:98px">
    <div class="card-photo" role="img" aria-label="Two electricians testing a wall panel" style="background:linear-gradient(135deg,#6d5a4a,#2f5a3c 55%,#a8a49a)"></div>
    <div class="card-caption">Click For More Details <svg width="12" height="12" viewBox="0 0 12 12"><circle cx="6" cy="6" r="6" fill="#5e2b8c"/><rect x="5.2" y="5" width="1.6" height="4.2" fill="#fff"/><rect x="5.2" y="2.6" width="1.6" height="1.5" fill="#fff"/></svg></div>
  </div>
  <div class="card" style="left:355px">
    <div class="card-photo" role="img" aria-label="Industrial plant room with rows of machinery" style="background:linear-gradient(180deg,#c7d3df,#7d8fa3 55%,#3e6a8e)"></div>
    <div class="card-caption">Click For More Details <svg width="12" height="12" viewBox="0 0 12 12"><circle cx="6" cy="6" r="6" fill="#5e2b8c"/><rect x="5.2" y="5" width="1.6" height="4.2" fill="#fff"/><rect x="5.2" y="2.6" width="1.6" height="1.5" fill="#fff"/></svg></div>
  </div>
  <div class="card" style="left:610px">
    <div class="card-photo" role="img" aria-label="Hand holding a meter over an electricity meter" style="background:linear-gradient(135deg,#8a4a3a,#6a7a3a 45%,#b9b9b4)"></div>
    <div class="card-caption">Click For More Details <svg width="12" height="12" viewBox="0 0 12 12"><circle cx="6" cy="6" r="6" fill="#5e2b8c"/><rect x="5.2" y="5" width="1.6" height="4.2" fill="#fff"/><rect x="5.2" y="2.6" width="1.6" height="1.5" fill="#fff"/></svg></div>
  </div>
  <div class="card" style="left:868px">
    <div class="card-photo" role="img" aria-label="Power line poles against a blue sky" style="background:linear-gradient(160deg,#3f7fd8,#1f5fc0)"></div>
    <div class="card-caption">Click For More Details <svg width="12" height="12" viewBox="0 0 12 12"><circle cx="6" cy="6" r="6" fill="#5e2b8c"/><rect x="5.2" y="5" width="1.6" height="4.2" fill="#fff"/><rect x="5.2" y="2.6" width="1.6" height="1.5" fill="#fff"/></svg></div>
  </div>
</section>

<footer class="site-footer">
  <div class="newsletter-panel"></div>
  <div class="newsletter abs">
    <h4>Newsletter</h4>
    <p>Subscribe our newsletter for more Details<br>About K7 Electrical Services</p>
    <div class="field">Name</div>
    <div class="field">Email</div>
    <span class="subscribe">Subscribe</span>
  </div>

  <div class="footer-col abs" style="left:481px">
    <h4>Quick links</h4>
    <ul><li>Home</li><li>About Us</li><li>Services</li><li>Blog</li><li>Contact Us</li></ul>
  </div>
  <div class="footer-col abs" style="left:674px">
    <h4>Other links</h4>
    <ul><li>All</li><li>Household</li><li>Organization</li><li>Research</li><li>Electrical Services</li></ul>
  </div>
  <div class="footer-col contact abs" style="left:867px">
    <h4>Contact Us</h4>
    <ul>
      <li><svg width="11" height="14" viewBox="0 0 12 16"><path fill="#999" d="M6 0a6 6 0 0 0-6 6c0 4.5 6 10 6 10s6-5.5 6-10a6 6 0 0 0-6-6zm0 8.3A2.3 2.3 0 1 1 6 3.7a2.3 2.3 0 0 1 0 4.6z"/></svg>Riverton, North Carolina 28000</li>
      <li><svg width="13" height="10" viewBox="0 0 14 11"><rect width="14" height="11" fill="#999"/><path d="M0 0 7 6 14 0" fill="none" stroke="#eee" stroke-width="1.4"/></svg>contact@k7electrical.com</li>
      <li><svg width="12" height="12" viewBox="0 0 24 24"><path fill="#999" d="M6.6 10.8a15 15 0 0 0 6.6 6.6l2.2-2.2a1 1 0 0 1 1-.25 11.4 11.4 0 0 0 3.6.57 1 1 0 0 1 1 1V20a1 1 0 0 1-1 1A17 17 0 0 1 3 4a1 1 0 0 1 1-1h3.5a1 1 0 0 1 1 1c0 1.25.2 2.45.57 3.57a1 1 0 0 1-.25 1z"/></svg>0230555147</li>
    </ul>
  </div>
</footer>

<section class="bottom-bar">
  <div class="social bottom-social abs"><span></span><span></span><span></span><span></span><span></span></div>
  <p class="copyright abs">Copyright © 2018 K7Electrical Services.All Rights Reserved | Terms | Policy.</p>
</section>

</body>
</html>
```